Networking Events Calendar/Diary

We need a responsive website that can act as both an online diary/calendar and a resource for community and networking events similar to brimtolvenquarrix.com (we do not want a clone, but one with similar functionality). We need to be able to host adverts, have a client area for clients to add their own events to the diary. This needs to have the functionality that clients have to pay to add recurring events. Some integration would be useful so that if a clients already has their own online diary on their website then using an API possibly to also add that event into our online diary

Industry/Entity Type

Events

Coding

Coded - Design and coding required

Number of Pages Required

5+ page

Requirements
Must have
• My project must have a calendar area, space for ads, be responsive and easily viewable on mobile. A subscribers area for clients and a way to purchase premium status so that premium events are highlighted.

```html
<!DOCTYPE html>
<html lang="en">
<head>
<meta charset="utf-8">
<title>KelvaEvents – Networking Events Diary</title>
<link href="https://fonts.googleapis.com/css2?family=Open+Sans:wght@400;600;700&display=swap" rel="stylesheet">
<style>
:root{
  --navy:#1b4a76;
  --navy-dark:#123a5e;
  --orange:#f5a31a;
  --text:#555;
  --heading:#1b4a76;
  --dark:#222;
  --line:#e2e2e2;
  --light:#f4f4f4;
  --avatar:#d9dde2;
  --footer:#1e5a8a;
  --footer-bottom:#174a73;
}
*{box-sizing:border-box;margin:0;padding:0}
html,body{width:1200px;height:3696px;overflow:hidden}
body{position:relative;background:#fff;font-family:"Open Sans",Arial,sans-serif;color:var(--text);font-size:12px}
.abs{position:absolute}
.ph{position:absolute;display:block}

/* header */
.site-header{left:0;top:0;width:1200px;height:118px}
.brand{left:99px;top:18px;font-size:38px;font-weight:400;color:var(--navy);letter-spacing:-1px;white-space:nowrap}
.tagline{left:99px;top:72px;font-size:12px;color:#444;white-space:nowrap}
.search-btn{left:584px;top:48px;width:34px;height:34px;border-radius:50%;background:#e8e8e8}
.header-links{left:638px;top:57px;font-size:12px;color:#333;display:flex;gap:40px;white-space:nowrap}
.login{left:1006px;top:48px;width:94px;height:36px;background:var(--orange);color:#fff;font-weight:700;font-size:12px;text-align:center;line-height:36px;border-radius:2px}

/* nav */
.main-nav{left:0;top:118px;width:1200px;height:54px;background:var(--navy);display:flex;padding-left:99px}
.main-nav a{color:#fff;text-decoration:none;font-size:15px;font-weight:600;line-height:54px;padding:0 25px;border-right:1px solid rgba(255,255,255,.15);white-space:nowrap}
.main-nav a.active{background:var(--navy-dark)}

/* hero */
.hero{left:0;top:172px;width:1200px;height:428px;background:linear-gradient(90deg,#6d6a66,#b8b4ae 45%,#e9e6e1 65%,#8a8580)}
.hero-title{left:134px;top:352px;font-size:30px;font-weight:700;color:#fff;white-space:nowrap}
.hero-sub{left:134px;top:394px;font-size:19px;color:#fff;width:470px;line-height:28px}
.hero-dots{left:568px;top:560px;display:flex;gap:8px}
.hero-dots i{width:8px;height:8px;border-radius:50%;background:rgba(255,255,255,.5)}
.hero-dots i.on{background:#fff}

/* section headings */
.sec-title{font-size:14px;font-weight:700;color:var(--heading);text-transform:uppercase;border-bottom:1px solid var(--line);padding-bottom:14px;width:714px}
.side-title{font-size:14px;font-weight:700;color:var(--heading);text-transform:uppercase;width:256px;border-bottom:1px solid var(--line);padding-bottom:10px}
.arrows{left:752px;top:636px;display:flex;gap:4px}
.arrows span{width:28px;height:28px;border:1px solid var(--line);display:block}

/* tips */
.tip{width:214px}
.tip .img{height:138px}
.tip h4{font-size:11px;font-weight:700;color:var(--dark);line-height:18px;margin-top:16px;text-transform:uppercase}
.tip p{font-size:11px;line-height:20px;margin-top:6px}

/* ad */
.ad-banner{left:148px;top:1306px;width:623px;height:79px;background:linear-gradient(90deg,#f2a51d,#e9e2c8 45%,#d57a1f)}

/* events */
.event{left:99px;width:714px;height:222px;border-bottom:1px solid var(--line)}
.event .img{left:0;top:0;width:214px;height:158px}
.event h3{position:absolute;left:248px;top:2px;font-size:12px;font-weight:700;color:var(--dark);text-transform:uppercase;white-space:nowrap}
.event .meta{position:absolute;left:248px;top:28px;font-size:10px;color:#888;display:flex;gap:28px}
.event p{position:absolute;left:248px;top:52px;width:466px;font-size:11px;line-height:24px}
.pager{left:422px;top:2565px;display:flex;gap:6px}
.pager span{height:26px;min-width:26px;padding:0 8px;border:1px solid #ddd;font-size:11px;line-height:24px;text-align:center;color:#333}

/* news */
.news{width:350px}
.news h3{font-size:13px;font-weight:700;color:var(--dark);line-height:22px;text-transform:uppercase}
.news .bar{width:50px;height:3px;background:var(--orange);margin:10px 0 14px}
.news p{font-size:12px;line-height:24px}

/* sidebar */
.promo{left:845px;width:256px;background:var(--navy);color:#fff;padding:20px 18px 0 20px}
.promo .icon{position:absolute;left:20px;top:22px;width:36px;height:36px;border:2px solid #fff;border-radius:50%}
.promo h5{margin-left:50px;font-size:13px;font-weight:700;line-height:18px}
.promo p{margin-left:20px;margin-top:8px;font-size:12px;line-height:18px}
.promo b{color:var(--orange);font-size:14px}
.social{left:845px;top:1020px;display:flex;gap:9px}
.social i{width:24px;height:24px;border-radius:50%;display:block}
.calendar{left:845px;top:1116px;width:256px;border:1px solid #ccc;background:#fff}
.cal-head{height:34px;background:#eee;text-align:center;font-weight:700;font-size:11px;line-height:34px;color:#333;position:relative}
.cal-head::before,.cal-head::after{content:"";position:absolute;top:2px;width:16px;height:30px;background:var(--navy)}
.cal-head::before{left:2px}.cal-head::after{right:2px}
.cal-grid{display:grid;grid-template-columns:repeat(7,1fr);gap:3px;padding:6px 6px 8px}
.cal-grid span{font-size:9px;text-align:center;height:22px;line-height:22px;border:1px solid #e4e4e4;color:#444}
.cal-grid span.dn{border:none;font-weight:700}
.cal-grid span.today{background:#9bbf6a;color:#fff}
.cal-grid span.empty{border:none}
.side-card{left:845px;width:256px}
.side-card .img{left:0;top:0;width:256px}
.side-card .cap{position:absolute;left:0;bottom:0;width:256px;height:60px;background:rgba(18,58,94,.9);color:#fff;padding:10px 18px}
.side-card .cap b{font-size:12px;display:block}
.side-card .cap span{font-size:10px}
.videos{left:845px;top:2134px;display:grid;grid-template-columns:123px 123px;gap:10px}
.videos i{display:block;height:90px;background:linear-gradient(135deg,#8a9bb0,#c9cfd6)}
.more-videos{left:845px;top:2457px;width:162px;height:37px;background:var(--orange);color:#fff;font-size:10px;font-weight:700;text-align:center;line-height:37px}
.tweets{left:845px;top:2518px;width:256px;height:456px;border:1px solid #ccc;background:#fff}
.tweets h6{font-size:13px;color:#333;padding:10px 12px;border-bottom:1px solid #ddd}
.tweets .follow{position:absolute;right:8px;top:9px;height:18px;padding:0 8px;border:1px solid #ccc;border-radius:3px;font-size:9px;line-height:16px;color:#333;background:#f4f4f4}
.tweet{display:flex;gap:10px;padding:12px 12px;height:93px}
.tweet .avatar{width:60px;height:60px;background:var(--avatar);flex:none}
.tweet p{font-size:10px;line-height:15px;color:#333}
.tweets .by{position:absolute;left:8px;bottom:8px;width:220px;height:24px;border:1px solid #ddd;font-size:9px;color:#888;padding:5px 6px}
.side-ad{left:845px;top:2999px;width:256px;height:217px;background:linear-gradient(180deg,#2f6db5,#e8b02a 60%,#2d64a8)}

/* footer */
.site-footer{left:0;top:3356px;width:1200px;height:266px;background:var(--footer);color:#fff}
.f-col{top:50px}
.f-col h4{font-size:19px;font-weight:400;margin-bottom:12px;white-space:nowrap}
.f-col li{list-style:none;font-size:12px;line-height:24px}
.f-col input{width:262px;height:32px;border:none;padding-left:12px;font-size:11px;font-family:inherit}
.f-col .btn{display:block;width:122px;height:38px;background:var(--orange);text-align:center;line-height:38px;font-size:13px;margin-top:12px}
.f-col .post{font-size:11px;line-height:16px;margin-bottom:14px;width:240px}
.footer-bottom{left:0;top:3622px;width:1200px;height:74px;background:var(--footer-bottom);color:#c8d6e4;font-size:11px;padding:30px 110px}
</style>
</head>
<body>

<header class="site-header abs">
  <div class="brand abs">KelvaEvents</div>
  <div class="tagline abs">We are an online diary/calendar and a resource for networking events</div>
  <div class="search-btn abs"></div>
  <div class="header-links abs"><span>Subscribe to our Weekly Bulletin</span><span>Register to Add Events</span></div>
  <div class="login abs">LOGIN</div>
</header>

<nav class="main-nav abs">
  <a class="active">HOME</a><a>LATEST NEWS</a><a>UPCOMING EVENT</a><a>OUR DIARY</a><a>CALENDAR</a><a>BLOG</a><a>CONTACT</a>
</nav>

<section class="hero abs" role="img" aria-label="Photo of people walking along a busy city street"></section>
<div class="hero-title abs">WELCOME TO KELVA EVENTS</div>
<div class="hero-sub abs">We are an online diary/calendar and a resource for networking events</div>
<div class="hero-dots abs"><i class="on"></i><i></i><i></i></div>

<h2 class="sec-title abs" style="left:99px;top:638px">Networking Tips</h2>
<div class="arrows abs"><span></span><span></span></div>

<article class="tip abs" style="left:99px;top:705px"><div class="img" role="img" aria-label="Photo of a crowded city square" style="background:linear-gradient(#b9b2a6,#7e7467)"></div><h4>Lorem Ipsum is simply dummy text of the printing</h4><p>Lorem Ipsum is simply dummy text of the printing and typesetting industry. been the industry's...</p></article>
<article class="tip abs" style="left:347px;top:705px"><div class="img" role="img" aria-label="Silhouette photo of a person on a pier" style="background:linear-gradient(#e6e6e6,#3a3a3a)"></div><h4>Lorem Ipsum is simply dummy text of the printing</h4><p>Lorem Ipsum is simply dummy text of the printing and typesetting industry. been the industry's...</p></article>
<article class="tip abs" style="left:596px;top:705px"><div class="img" role="img" aria-label="Photo of an airport escalator" style="background:linear-gradient(#d8d8d8,#4a4a4a)"></div><h4>Lorem Ipsum is simply dummy text of the printing</h4><p>Lorem Ipsum is simply dummy text of the printing and typesetting industry. been the industry's...</p></article>
<article class="tip abs" style="left:99px;top:998px"><div class="img" role="img" aria-label="Photo of a car dashboard on the road" style="background:linear-gradient(#9fb4c8,#2d2d2d)"></div><h4>Lorem Ipsum is simply dummy text of the printing</h4><p>Lorem Ipsum is simply dummy text of the printing and typesetting industry. been the industry's...</p></article>
<article class="tip abs" style="left:347px;top:998px"><div class="img" role="img" aria-label="Photo of an airplane in the sky" style="background:linear-gradient(#dfe6ee,#b6c3d1)"></div><h4>Lorem Ipsum is simply dummy text of the printing</h4><p>Lorem Ipsum is simply dummy text of the printing and typesetting industry. been the industry's...</p></article>
<article class="tip abs" style="left:596px;top:998px"><div class="img" role="img" aria-label="Photo of an old world map with a passport" style="background:linear-gradient(#8a5a2c,#3e2814)"></div><h4>Lorem Ipsum is simply dummy text of the printing</h4><p>Lorem Ipsum is simply dummy text of the printing and typesetting industry. been the industry's...</p></article>

<div class="ad-banner abs" role="img" aria-label="Advertising banner for free video tutorials"></div>

<h2 class="sec-title abs" style="left:99px;top:1418px">Upcoming Events</h2>

<article class="event abs" style="top:1488px"><div class="img ph" role="img" aria-label="Photo of a canal city" style="background:linear-gradient(#a9c3dc,#8c6a45)"></div><h3>Lorem Ipsum is simply dummy ext of the printing</h3><div class="meta"><span>27 March 2015</span><span>128</span><span>265</span></div><p>Lorem Ipsum is simply dummy text of the printing and typesetting industry. Lorem Ipsum has been the industry's standard dummy text ever since the 1500s, when an unknown printer took a galley of type and scrambled it to make a type specimen book. It has survived not only five centuries, but also the leap...</p></article>
<article class="event abs" style="top:1710px"><div class="img ph" role="img" aria-label="Photo of a high-speed train" style="background:linear-gradient(#c9c9c9,#6a5a50)"></div><h3>Lorem Ipsum is simply dummy ext of the printing</h3><div class="meta"><span>27 March 2015</span><span>128</span><span>265</span></div><p>Lorem Ipsum is simply dummy text of the printing and typesetting industry. Lorem Ipsum has been the industry's standard dummy text ever since the 1500s, when an unknown printer took a galley of type and scrambled it to make a type specimen book. It has survived not only five centuries, but also the leap...</p></article>
<article class="event abs" style="top:1932px"><div class="img ph" role="img" aria-label="Photo of colleagues at a laptop" style="background:linear-gradient(#d6d2cc,#6d7b8c)"></div><h3>Lorem Ipsum is simply dummy ext of the printing</h3><div class="meta"><span>27 March 2015</span><span>128</span><span>265</span></div><p>Lorem Ipsum is simply dummy text of the printing and typesetting industry. Lorem Ipsum has been the industry's standard dummy text ever since the 1500s, when an unknown printer took a galley of type and scrambled it to make a type specimen book. It has survived not only five centuries, but also the leap...</p></article>
<article class="event abs" style="top:2154px"><div class="img ph" role="img" aria-label="Photo of two businesswomen talking" style="background:linear-gradient(#b7c4d2,#3b3f46)"></div><h3>Lorem Ipsum is simply dummy ext of the printing</h3><div class="meta"><span>27 March 2015</span><span>128</span><span>265</span></div><p>Lorem Ipsum is simply dummy text of the printing and typesetting industry. Lorem Ipsum has been the industry's standard dummy text ever since the 1500s, when an unknown printer took a galley of type and scrambled it to make a type specimen book. It has survived not only five centuries, but also the leap...</p></article>
<article class="event abs" style="top:2375px;border-bottom:none"><div class="img ph" role="img" aria-label="Photo of a man in glasses and bow tie" style="background:linear-gradient(#e8e2da,#b8423a)"></div><h3>Lorem Ipsum is simply dummy ext of the printing</h3><div class="meta"><span>27 March 2015</span><span>128</span><span>265</span></div><p>Lorem Ipsum is simply dummy text of the printing and typesetting industry. Lorem Ipsum has been the industry's standard dummy text ever since the 1500s, when an unknown printer took a galley of type and scrambled it to make a type specimen book. It has survived not only five centuries, but also the leap...</p></article>

<div class="pager abs"><span>Prev</span><span>1</span><span>2</span><span>3</span><span>4</span><span>5</span><span>6</span><span>...</span><span>22</span><span>Next</span></div>

<h2 class="sec-title abs" style="left:99px;top:2640px">Networking News</h2>
<article class="news abs" style="left:99px;top:2706px"><h3>Lorem Ipsum is simply dummy ext<br>of the printing</h3><div class="bar"></div><p>Lorem Ipsum is simply dummy text of the printing and typesetting industry. Lorem Ipsum has been the industry's standard dummy text ever since the 1500s, when an unknown printer took a galley...</p></article>
<article class="news abs" style="left:480px;top:2706px"><h3>Lorem Ipsum is simply dummy ext<br>of the printing</h3><div class="bar"></div><p>Lorem Ipsum is simply dummy text of the printing and typesetting industry. Lorem Ipsum has been the industry's standard dummy text ever since the 1500s, when an unknown printer took a galley...</p></article>
<article class="news abs" style="left:99px;top:2916px"><h3>Lorem Ipsum is simply dummy ext<br>of the printing</h3><div class="bar"></div><p>Lorem Ipsum is simply dummy text of the printing and typesetting industry. Lorem Ipsum has been the industry's standard dummy text ever since the 1500s, when an unknown printer took a galley...</p></article>
<article class="news abs" style="left:480px;top:2916px"><h3>Lorem Ipsum is simply dummy ext<br>of the printing</h3><div class="bar"></div><p>Lorem Ipsum is simply dummy text of the printing and typesetting industry. Lorem Ipsum has been the industry's standard dummy text ever since the 1500s, when an unknown printer took a galley...</p></article>
<article class="news abs" style="left:99px;top:3125px"><h3>Lorem Ipsum is simply dummy ext<br>of the printing</h3><div class="bar"></div><p>Lorem Ipsum is simply dummy text of the printing and typesetting industry. Lorem Ipsum has been the industry's standard dummy text ever since the 1500s, when an unknown printer took a galley...</p></article>
<article class="news abs" style="left:480px;top:3125px"><h3>Lorem Ipsum is simply dummy ext<br>of the printing</h3><div class="bar"></div><p>Lorem Ipsum is simply dummy text of the printing and typesetting industry. Lorem Ipsum has been the industry's standard dummy text ever since the 1500s, when an unknown printer took a galley...</p></article>

<aside>
  <div class="promo abs" style="top:641px;height:128px"><span class="icon"></span><h5>COMMUNITY<br>EVENTS</h5><p>community events and one off events would be <b>FREE</b></p></div>
  <div class="promo abs" style="top:786px;height:131px"><span class="icon"></span><h5>BUSINESS AND<br>COMMERCIAL EVENTS</h5><p>would be <b>CHARGEABLE</b></p></div>

  <h3 class="side-title abs" style="left:845px;top:940px">Follow Us</h3>
  <div class="abs" style="left:845px;top:988px;font-size:10px">Connect with our social media</div>
  <div class="social abs"><i style="background:#3b5998"></i><i style="background:#3fa9e0"></i><i style="background:#d9423a"></i><i style="background:#0e76a8"></i><i style="background:#e0a020"></i><i style="background:#c4302b"></i><i style="background:#cb2027"></i></div>

  <h3 class="side-title abs" style="left:845px;top:1072px">My Event Diary</h3>
  <div class="calendar abs">
    <div class="cal-head">DECEMBER</div>
    <div class="cal-grid">
      <span class="dn">Mon</span><span class="dn">Tue</span><span class="dn">Wed</span><span class="dn">Thu</span><span class="dn">Fri</span><span class="dn">Sat</span><span class="dn">Sun</span>
      <span>1</span><span>2</span><span>3</span><span>4</span><span>5</span><span>6</span><span>7</span>
      <span>8</span><span>9</span><span>10</span><span>11</span><span>12</span><span>13</span><span>14</span>
      <span>15</span><span>16</span><span>17</span><span>18</span><span>19</span><span>20</span><span>21</span>
      <span>22</span><span>23</span><span>24</span><span>25</span><span>26</span><span>27</span><span>28</span>
      <span>29</span><span class="today">30</span><span>31</span><span class="empty"></span><span class="empty"></span><span class="empty"></span><span class="empty"></span>
    </div>
  </div>

  <div class="side-card abs" style="top:1338px;height:239px"><div class="img ph" role="img" aria-label="Photo of a person typing on a laptop" style="height:239px;background:linear-gradient(#cfd6de,#7d8896)"></div><div class="cap"><b>SUBSCRIBE</b><span>Subscribe to our event ›</span></div></div>
  <div class="side-card abs" style="top:1594px;height:229px"><div class="img ph" role="img" aria-label="Photo of a smiling woman at a desk" style="height:229px;background:linear-gradient(#f0ede8,#a89a8a)"></div><div class="cap"><b>REGISTER</b><span>Register to Add Events ›</span></div></div>
  <div class="side-card abs" style="top:1848px;height:217px"><div class="img ph" role="img" aria-label="Web hosting advertisement" style="height:217px;background:linear-gradient(#1d5fa8,#f2f4f7 55%,#1a3e6c)"></div></div>

  <h3 class="side-title abs" style="left:845px;top:2094px">Video Gallery</h3>
  <div class="videos abs" role="img" aria-label="Grid of six video thumbnails"><i></i><i></i><i></i><i></i><i></i><i></i></div>
  <div class="more-videos abs">VIEW MORE VIDEOS</div>

  <div class="tweets abs">
    <h6>Tweets</h6>
    <span class="follow">Follow</span>
    <div class="tweet"><div class="avatar"></div><p>Lorem Ipsum is simply dummy text of the printing and typesetting...</p></div>
    <div class="tweet"><div class="avatar"></div><p>Lorem Ipsum is simply dummy text of the printing and typesetting...</p></div>
    <div class="tweet"><div class="avatar"></div><p>Lorem Ipsum is simply dummy text of the printing and typesetting...</p></div>
    <div class="tweet"><div class="avatar"></div><p>Lorem Ipsum is simply dummy text of the printing and typesetting...</p></div>
    <div class="by">Tweet to @kelvaevents</div>
  </div>

  <div class="side-ad abs" role="img" aria-label="Family account advertisement"></div>
</aside>

<footer class="site-footer abs">
  <div class="f-col abs" style="left:108px"><h4>Quick links</h4><ul><li>About Us</li><li>What We Do</li><li>How we work</li><li>Blog Post</li><li>News &amp; Events</li></ul></div>
  <div class="f-col abs" style="left:335px"><h4>Resources</h4><ul><li>Mauris vel lacus</li><li>Vitae felis vestibulum</li><li>Aoluptat imperdiet</li><li>Cum sociis</li><li>Natoque penatibus</li></ul></div>
  <div class="f-col abs" style="left:537px"><h4>Newsletters Sign Up</h4><p style="font-size:12px;margin-bottom:12px">Please sign up here for latest news</p><input placeholder="Email address"><span class="btn">Subscribe</span></div>
  <div class="f-col abs" style="left:855px"><h4>Follow Us</h4>
    <p class="post">Lorem Ipsum is simply dummy text of the http://www.pressvaleworks.com</p>
    <p class="post">Lorem Ipsum is simply dummy text of the http://www.pressvaleworks.com</p>
    <p class="post">Lorem Ipsum is simply dummy text of the http://www.pressvaleworks.com</p>
  </div>
</footer>
<div class="footer-bottom abs">© 2015 Company Name. All right reserved. Term of Use</div>

</body>
</html>
```